High-End Print/Digital Ad for Unique Luxury Travel Company Required

Objective:
Design a compelling and visually striking advertisement that highlights our company’s unmatched luxury travel experiences. The ad should elevate our brand image, spark curiosity, and drive prospective clients to contact us.
Target Audience:
• Affluent individuals seeking extraordinary, tailor-made travel experiences
• Affluent, luxury, high-net-worth individuals looking for value, expertise, and white-glove service
• Professionals or retirees who appreciate unique, thoughtfully curated travel over mainstream tourism
Key Messages to Communicate:
• One-of-a-kind luxury travel: Once-in-a-lifetime experiences that are curated with creativity and meticulous attention to detail
• Exceptional service: White-glove, personalized planning from start to finish
• 38 years’ travel experience – expert knowledge of destinations, modes of travel, premium accommodations and well-established, meaningful industry connections.
• Highly trusted: Cruise line executives often say, “No one does what you do.”
Tone and Style:
• Elegant, luxurious, sophisticated
• Eye-catching, polished, and modern
• Professional but warm—conveys trust and credibility
• High-impact visuals (full-bleed imagery, custom graphics, or high-end photography)
Deliverables:
• One full-page print ad and digital ad
• Ready-to-print, high-resolution file + working file (PSD, AI, etc.)
Optional: Social media-optimized version or short motion-graphic variation (if designer offers it)
Inspiration & Visual Style Suggestions:
• Think Lumen Voyages, Harrow Pike Wanderer, Silver Quill, or Orvel Retreats ad styles
• Large, emotive imagery with elegant typography
• Clean layout that speaks luxury, clarity, and trust
Copy Direction (draft):
For those who’ve explored the world—and crave something beyond the ordinary.
Each journey is a masterfully curated experience, rich in detail, seamless in execution, and unforgettable in every way.
Founded in 1997, Tidewell Journeys is a unique travel company specializing in cruising, all-inclusive luxury properties, and tours world-wide for individuals, groups, and incentives.
We offer an exceptional range of services designed to ensure every journey is flawlessly executed and truly unforgettable.
Let us help you plan your next extraordinary adventure.
Note: You may refine the copy slightly based on layout or format needs.
Other Resources for References:
1. Website - www.tidewelljourneys-example.com

```html
<!DOCTYPE html>
<html lang="en">
<head>
<meta charset="utf-8">
<title>Tidewell Journeys — Ad Suite</title>
<link rel="stylesheet" href="https://fonts.googleapis.com/css2?family=Playfair+Display:wght@500;600&family=Montserrat:wght@300;400&display=swap">
<style>
  :root {
    --board: #dedede;
    --label: #4a4a4a;
    --rule: #555555;
    --ink-light: #ffffff;
    --ink-soft: #e6e6e6;
    --sky: #1d3c58;
    --sky-deep: #13263a;
    --glow: #d9953f;
    --glow-hot: #f0b660;
    --sea: #12222f;
    --sea-deep: #05090d;
    --serif: "Playfair Display", Georgia, serif;
    --sans: "Montserrat", Arial, sans-serif;
  }
  * { margin: 0; padding: 0; box-sizing: border-box; }
  html, body { width: 1200px; height: 800px; overflow: hidden; background: var(--board); }
  .board { position: relative; width: 1200px; height: 800px; }

  .format-label {
    position: absolute; right: 47px;
    font-family: var(--sans); font-weight: 400; font-size: 15px;
    letter-spacing: 0.5px; color: var(--label); line-height: 1;
  }
  .leaders { position: absolute; inset: 0; }

  .ad { position: absolute; overflow: hidden; color: var(--ink-light); }
  .ad .photo { position: absolute; inset: 0; width: 100%; height: 100%; display: block; }
  .headline {
    position: absolute; font-family: var(--serif); font-weight: 600;
    text-transform: uppercase; letter-spacing: 0.5px;
  }
  .subline {
    position: absolute; font-family: var(--serif); font-weight: 500;
    text-transform: uppercase; letter-spacing: 0.6px;
  }
  .brand-name {
    position: absolute; font-family: var(--serif); font-weight: 500;
    text-transform: uppercase; letter-spacing: 1px; white-space: nowrap; line-height: 1;
  }

  /* print */
  .ad-print { left: 42px; top: 41px; width: 510px; height: 718px; }
  .ad-print .headline { left: 0; width: 100%; top: 336px; text-align: center; font-size: 38px; line-height: 37px; }
  .ad-print .subline { left: 0; width: 100%; top: 460px; text-align: center; font-size: 14px; }
  .ad-print .rule-top { position: absolute; left: 133px; width: 244px; top: 524px; height: 1px; background: var(--ink-soft); }
  .ad-print .body-copy {
    position: absolute; left: 0; width: 100%; top: 533px; text-align: center;
    font-family: var(--sans); font-weight: 300; font-size: 10px; line-height: 13.3px; color: var(--ink-soft);
  }
  .ad-print .body-copy p + p { margin-top: 5px; }
  .ad-print .web-row {
    position: absolute; left: 133px; width: 244px; top: 620px;
    display: flex; align-items: center; gap: 6px;
    font-family: var(--sans); font-weight: 300; font-size: 9.5px; color: var(--ink-soft);
  }
  .ad-print .web-row .line { flex: 1; height: 1px; background: var(--ink-soft); }
  .ad-print .brand-name { left: 0; width: 100%; text-align: center; top: 677px; font-size: 17px; }

  /* banner */
  .ad-banner { left: 780px; top: 203px; width: 373px; height: 141px; }
  .ad-banner .headline { left: 13px; top: 12px; font-size: 22.5px; line-height: 23px; }
  .ad-banner .subline { left: 13px; top: 106px; font-size: 7.5px; line-height: 12px; }
  .ad-banner .brand-name { right: 11px; top: 13px; font-size: 8.5px; }

  /* social */
  .ad-social { left: 780px; top: 386px; width: 373px; height: 373px; }
  .ad-social .headline { left: 0; width: 100%; top: 231px; text-align: center; font-size: 30.5px; line-height: 31px; }
  .ad-social .subline { left: 0; width: 100%; top: 332px; text-align: center; font-size: 11.5px; }
  .ad-social .brand-name { right: 12px; top: 17px; font-size: 12px; }
</style>
</head>
<body>
<main class="board">
  <svg class="leaders" width="1200" height="800" aria-hidden="true">
    <g stroke="var(--rule)" stroke-width="1" fill="none">
      <line x1="564" y1="58" x2="1067" y2="58"/>
      <polyline points="1000,93 699,93 699,398 767,398"/>
      <polyline points="979,127 734,127 734,221 767,221"/>
    </g>
    <g fill="var(--rule)">
      <circle cx="564" cy="58" r="4"/>
      <circle cx="767" cy="398" r="4"/>
      <circle cx="767" cy="221" r="4"/>
    </g>
  </svg>
  <span class="format-label" style="top:51px">PRINT AD</span>
  <span class="format-label" style="top:86px">SOCIAL MEDIA AD</span>
  <span class="format-label" style="top:120px">DIGITAL BANNER AD</span>

  <svg width="0" height="0" aria-hidden="true" style="position:absolute">
    <defs>
      <linearGradient id="sceneTall" x1="0" y1="0" x2="0" y2="1">
        <stop offset="0" stop-color="var(--sky-deep)"/>
        <stop offset="0.14" stop-color="var(--sky)"/>
        <stop offset="0.27" stop-color="#5a4a3c"/>
        <stop offset="0.31" stop-color="var(--glow-hot)"/>
        <stop offset="0.34" stop-color="#2a4660"/>
        <stop offset="0.42" stop-color="var(--glow)"/>
        <stop offset="0.5" stop-color="#1b2e3c"/>
        <stop offset="0.7" stop-color="var(--sea)"/>
        <stop offset="1" stop-color="var(--sea-deep)"/>
      </linearGradient>
      <linearGradient id="sceneWide" x1="0" y1="0" x2="1" y2="1">
        <stop offset="0" stop-color="var(--sky-deep)"/>
        <stop offset="0.45" stop-color="#2b4a66"/>
        <stop offset="0.7" stop-color="var(--glow)"/>
        <stop offset="0.85" stop-color="#223a4e"/>
        <stop offset="1" stop-color="var(--sea)"/>
      </linearGradient>
      <linearGradient id="sceneSquare" x1="0" y1="0" x2="0" y2="1">
        <stop offset="0" stop-color="var(--sky-deep)"/>
        <stop offset="0.2" stop-color="var(--sky)"/>
        <stop offset="0.46" stop-color="#2c4a64"/>
        <stop offset="0.52" stop-color="var(--glow-hot)"/>
        <stop offset="0.6" stop-color="#2a3e4e"/>
        <stop offset="0.75" stop-color="#14232f"/>
        <stop offset="1" stop-color="var(--sea-deep)"/>
      </linearGradient>
    </defs>
  </svg>

  <article class="ad ad-print">
    <svg class="photo" viewBox="0 0 510 718" preserveAspectRatio="none" role="img" aria-label="Photo of a luxury cruise ship lit at dusk on calm water, golden sunset on the horizon, dark sea below">
      <rect width="510" height="718" fill="url(#sceneTall)"/>
    </svg>
    <h1 class="headline">For those<br>who've explored<br>the world</h1>
    <p class="subline">And crave something beyond the ordinary.</p>
    <div class="rule-top"></div>
    <div class="body-copy">
      <p>Each journey is a masterfully curated experience,<br>rich in detail, seamless in execution,<br>and unforgettable in every way.</p>
      <p>We offer an exceptional range of services<br>designed to ensure every journey is flawlessly<br>executed and truly unforgettable.</p>
    </div>
    <div class="web-row"><span class="line"></span><span>www.tidewelljourneys-example.com</span><span class="line"></span></div>
    <div class="brand-name">Tidewell Journeys</div>
  </article>

  <article class="ad ad-banner">
    <svg class="photo" viewBox="0 0 373 141" preserveAspectRatio="none" role="img" aria-label="Photo of a luxury cruise ship at sunset on calm water">
      <rect width="373" height="141" fill="url(#sceneWide)"/>
    </svg>
    <h2 class="headline">For those<br>who've<br>explored<br>the world</h2>
    <p class="subline">And crave something beyond<br>the ordinary.</p>
    <div class="brand-name">Tidewell Journeys</div>
  </article>

  <article class="ad ad-social">
    <svg class="photo" viewBox="0 0 373 373" preserveAspectRatio="none" role="img" aria-label="Photo of a luxury cruise ship lit at dusk, golden sunset reflecting on the sea">
      <rect width="373" height="373" fill="url(#sceneSquare)"/>
    </svg>
    <div class="brand-name">Tidewell Journeys</div>
    <h2 class="headline">For those<br>who've explored<br>the world</h2>
    <p class="subline">And crave something beyond the ordinary.</p>
  </article>
</main>
</body>
</html>
```